Letterhead & Greeting Card Design Project

I need a few files prepared for dynamic digital printing: letterhead and 2 postcards with an envelope for each. Enclosed are specific directions from the printer for each file and overall. I have also enclosed mockups of what I would like on those designs and some raw files to work with.

Industry/Entity Type

Digital

```html
<!DOCTYPE html>
<html lang="en">
<head>
<meta charset="utf-8">
<title>Lumora Media – Envelope</title>
<link rel="stylesheet" href="https://fonts.googleapis.com/css2?family=Titillium+Web:wght@400;600&display=swap">
<style>
  :root {
    --paper: #ffffff;
    --ink: #1e1e1e;
    --brand-grey: #5a5a5a;
    --brand-blue: #5bbde0;
    --dot-grey: #a9a9a9;
  }
  html, body {
    margin: 0;
    padding: 0;
    overflow: hidden;
    background: var(--paper);
  }
  .envelope {
    position: relative;
    width: 1200px;
    height: 700px;
    background: var(--paper);
    font-family: "Titillium Web", Arial, sans-serif;
    color: var(--ink);
    overflow: hidden;
  }
  .brand {
    position: absolute;
    left: 64px;
    top: 30px;
    display: flex;
    align-items: center;
    gap: 14px;
  }
  .brand-dot {
    width: 30px;
    height: 30px;
    border-radius: 50%;
    background: var(--brand-blue);
  }
  .brand-name {
    font-size: 44px;
    font-weight: 600;
    line-height: 1;
    color: var(--brand-grey);
    letter-spacing: 0.5px;
  }
  .return-address {
    position: absolute;
    left: 64px;
    top: 100px;
    margin: 0;
    font-style: normal;
    font-size: 30px;
    line-height: 38px;
  }
  .recipient {
    position: absolute;
    left: 386px;
    top: 330px;
    margin: 0;
    font-style: normal;
    font-size: 30px;
    line-height: 38px;
  }
  .recipient span {
    display: block;
    margin-bottom: 37px;
  }
  .corner-accent {
    position: absolute;
    left: 0;
    top: 520px;
    width: 220px;
    height: 180px;
    border-top-right-radius: 120px;
    background: linear-gradient(120deg, var(--dot-grey) 0%, #c9d7dd 55%, var(--brand-blue) 100%);
    opacity: 0.55;
  }
</style>
</head>
<body>
  <main class="envelope">
    <div class="brand">
      <span class="brand-name">Lumora Media</span>
      <span class="brand-dot"></span>
    </div>

    <address class="return-address">
      John Doe<br>
      Company<br>
      Street<br>
      City, State/Province, Zip/Postal Code
    </address>

    <address class="recipient">
      <span>Jane Jones</span>
      <span>Account Name</span>
      <span>Street</span>
      <span>City, State/Province, Zip/Postal Code</span>
    </address>

    <div class="corner-accent" role="img" aria-label="Decorative cluster of grey and blue dots in the lower left corner"></div>
  </main>
</body>
</html>
```